Detail Shop Business card design

i need a business card design for my new detailing company called 'Brisk's Polish Works'. i want an all black and white design . simple, direct and to the point. i want the designer to choose a fitting font to match the logothe front should have logo, address, phone and email and the back side should have a slogan and text indicating that we offer services on anything including cars, trucks, motorcycles and RVs. slogan will read "we take pride in your ride"
maybe also very small on the back side the IG icon with Brisks_Polish_Works

phone 208.417.6352
address 3847 E Larkin Ave
Spokane WA 99214
email: BrisksPolish@mailvexo.com

Target Market(s)

all ages , auto enthusiasts

Industry/Entity Type

Automotive

Contact Information for Business Card

the front should have logo, address, phone and email and the back side should have a slogan and text indicating that we offer services on anything including cars, trucks, motorcycles and RVs. slogan will read "we take pride in your ride"

phone 208.417.6352
address 3847 E Larkin Ave
Spokane WA 99214

Colors
000000
ffffff

Requirements
Must have
• bold font and very simple design with good spacing
Nice to have
• anything creative from the designer indicating we service any types of vehicles
Should not have
• any colors ,

```html
<!DOCTYPE html>
<html lang="en">
<head>
<meta charset="utf-8">
<title>Brisk's Polish Works — Business Card</title>
<link rel="stylesheet" href="https://fonts.googleapis.com/css2?family=Bitter:wght@400;500;700&display=swap">
<style>
  :root {
    --backdrop: #1c1c1c;
    --ink: #111111;
    --paper: #ffffff;
    --card-dark: #141414;
    --art-light: #d9d9d9;
    --art-dark: #2a2a2a;
  }
  * { margin: 0; padding: 0; box-sizing: border-box; }
  html, body {
    width: 1200px; height: 897px; overflow: hidden;
    background: var(--backdrop);
    font-family: "Bitter", Georgia, serif;
  }
  .stage { position: relative; width: 1200px; height: 897px; }

  .card {
    position: absolute; left: 326px; width: 543px; height: 311px;
    border-radius: 16px;
  }
  .card--front { top: 127px; background: var(--paper); color: var(--ink); }
  .card--back { top: 475px; background: var(--card-dark); color: var(--paper); }

  .brand {
    position: absolute; left: 380px; top: 196px; width: 168px; height: 160px;
    display: flex; flex-direction: column; align-items: center; justify-content: center;
    gap: 10px; text-align: center;
  }
  .card .brand { left: 54px; top: 69px; }
  .brand__dot { width: 14px; height: 14px; border-radius: 50%; background: var(--ink); }
  .brand__name { font-weight: 700; font-size: 23px; line-height: 1.15; color: var(--ink); }

  .divider {
    position: absolute; left: 264px; top: 83px; width: 2px; height: 144px;
    background: var(--ink);
  }

  .contact { position: absolute; left: 304px; top: 78px; }
  .contact__name { font-size: 21px; font-weight: 500; letter-spacing: 0.5px; line-height: 1.1; }
  .contact__role { font-size: 13px; margin-top: 2px; }
  .contact__address { font-size: 14px; line-height: 18px; margin-top: 15px; }
  .contact__lines { list-style: none; margin-top: 11px; font-size: 14px; line-height: 18px; }
  .contact__lines li { display: flex; align-items: center; gap: 6px; }
  .contact__lines svg { width: 9px; height: 9px; flex: none; }

  .hero-art {
    position: absolute; left: 36px; top: 55px; width: 470px; height: 182px;
    background: radial-gradient(ellipse at 55% 50%, var(--art-light) 0%, #8a8a8a 40%, var(--art-dark) 75%, transparent 100%);
    border-radius: 40px;
  }
  .tagline {
    position: absolute; left: 0; right: 0; top: 253px;
    text-align: center; text-transform: uppercase; font-size: 13px; letter-spacing: 0.4px;
  }
  .tagline__slogan { font-weight: 500; }
  .tagline__services { margin-top: 9px; }
</style>
</head>
<body>
<main class="stage">
  <section class="card card--front" aria-label="Business card front">
    <div class="brand">
      <span class="brand__dot"></span>
      <span class="brand__name">Brisk's<br>Polish Works</span>
    </div>
    <div class="divider"></div>
    <div class="contact">
      <p class="contact__name">DARREN HOLT</p>
      <p class="contact__role">Director</p>
      <p class="contact__address">3847 E Larkin Ave<br>Spokane WA 99214</p>
      <ul class="contact__lines">
        <li><svg viewBox="0 0 10 10"><path d="M2 0.5 L3.6 2.6 L2.7 3.6 Q3.6 5.8 6.3 7.3 L7.4 6.4 L9.5 8 L8.3 9.5 Q3.5 9 0.5 1.8 Z" fill="#111"/></svg>208.417.6352</li>
        <li><svg viewBox="0 0 10 10"><rect x="0.7" y="2" width="8.6" height="6" fill="none" stroke="#111"/><path d="M0.7 2 L5 5.5 L9.3 2" fill="none" stroke="#111"/></svg>BrisksPolish@mailvexo.com</li>
        <li><svg viewBox="0 0 10 10"><circle cx="5" cy="5" r="4.3" fill="none" stroke="#111"/><ellipse cx="5" cy="5" rx="1.8" ry="4.3" fill="none" stroke="#111"/><path d="M0.7 5 H9.3" stroke="#111"/></svg>www.BrisksPolishWorks.com</li>
      </ul>
    </div>
  </section>

  <section class="card card--back" aria-label="Business card back">
    <div class="hero-art" role="img" aria-label="White hot rod illustration in front of a pale sun circle"></div>
    <div class="tagline">
      <p class="tagline__slogan">We take pride in your ride</p>
      <p class="tagline__services">Cars - Trucks - Motorcycles and RVs</p>
    </div>
  </section>
</main>
</body>
</html>
```